Business Card Design

New business card design

Target Market(s)

Residential & Commercial Property Managers

Industry/Entity Type

Plumbing Services

Contact Information for Business Card

Name - Rowan Keddle, title - Director, Phone Number - 0431 286 517, email - rowan@tbk-plumbing.com.au, Company ABN - 73 215 904 386,

Font styles to use
Sans Serif

Colors
0054AA
0677BA
7BADD7
CADEEF
E8F1F8

```html
<!DOCTYPE html>
<html lang="en">
<head>
<meta charset="utf-8">
<title>TBK Plumbing Services – Business Card</title>
<link href="https://fonts.googleapis.com/css2?family=Montserrat:wght@300;400;600;700&display=swap" rel="stylesheet">
<style>
  :root {
    --stage: #2a2b2d;
    --card-top: #222a34;
    --card-bottom: #1a2029;
    --edge: #2fa4e0;
    --accent: #2a9ad8;
    --logo-dim: #3f5f8e;
    --tagline: #4d5560;
    --ink: #f2f5f8;
    --ink-soft: #d7dde4;
  }
  * { margin: 0; padding: 0; box-sizing: border-box; }
  html, body { width: 1200px; height: 900px; overflow: hidden; }
  body {
    background: var(--stage);
    font-family: "Montserrat", sans-serif;
    display: flex;
    flex-direction: column;
    align-items: center;
    justify-content: center;
    gap: 44px;
  }
  .card {
    position: relative;
    width: 630px;
    height: 360px;
    border-radius: 22px;
    background: linear-gradient(160deg, var(--card-top), var(--card-bottom));
    box-shadow: 0 5px 0 var(--edge), 0 14px 30px rgba(0,0,0,.45);
    overflow: hidden;
  }

  /* Brand wordmark */
  .brand { display: flex; flex-direction: column; align-items: center; }
  .brand-row { display: flex; align-items: center; gap: 10px; }
  .brand-name { font-weight: 300; letter-spacing: 4px; line-height: 1; }
  .brand-dot { border-radius: 50%; background: var(--accent); }
  .brand-tagline {
    font-weight: 400;
    color: var(--tagline);
    text-transform: lowercase;
  }

  /* Front */
  .card-front { display: flex; align-items: center; justify-content: center; }
  .card-front .brand-name { font-size: 120px; color: var(--logo-dim); }
  .card-front .brand-dot { width: 22px; height: 22px; margin-top: 60px; }
  .card-front .brand-tagline { font-size: 15px; letter-spacing: 17px; margin-top: 14px; margin-left: 17px; }

  /* Back */
  .card-back { display: flex; align-items: center; padding: 0 0 0 62px; }
  .card-back .brand { width: 200px; }
  .card-back .brand-name { font-size: 64px; color: var(--ink); }
  .card-back .brand-dot { width: 12px; height: 12px; margin-top: 32px; }
  .card-back .brand-tagline { font-size: 8px; letter-spacing: 7px; margin-top: 8px; margin-left: 7px; }
  .divider { width: 2px; height: 168px; background: var(--accent); margin: 0 30px 0 34px; }
  .contact { color: var(--ink); }
  .contact-name { font-size: 25px; font-weight: 700; color: var(--accent); line-height: 1.1; }
  .contact-title { font-size: 14px; font-weight: 400; color: var(--ink-soft); margin: 2px 0 12px 16px; }
  .contact-list { list-style: none; margin-left: 16px; }
  .contact-list li { display: flex; align-items: center; gap: 10px; font-size: 14px; font-weight: 400; margin-bottom: 7px; }
  .contact-list svg { width: 14px; height: 14px; fill: var(--accent); flex: none; }
  .contact-abn { font-size: 14px; margin: 8px 0 0 16px; }
  .contact-abn strong { font-weight: 700; }
</style>
</head>
<body>

<section class="card card-front">
  <div class="brand">
    <div class="brand-row">
      <span class="brand-name">tbk</span>
      <span class="brand-dot"></span>
    </div>
    <span class="brand-tagline">plumbing services</span>
  </div>
</section>

<section class="card card-back">
  <div class="brand">
    <div class="brand-row">
      <span class="brand-name">tbk</span>
      <span class="brand-dot"></span>
    </div>
    <span class="brand-tagline">plumbing services</span>
  </div>
  <div class="divider"></div>
  <div class="contact">
    <p class="contact-name">Rowan Keddle</p>
    <p class="contact-title">Director</p>
    <ul class="contact-list">
      <li>
        <svg viewBox="0 0 24 24"><path d="M6.6 10.8a15.1 15.1 0 0 0 6.6 6.6l2.2-2.2c.3-.3.7-.4 1-.2 1.1.4 2.3.6 3.6.6.6 0 1 .4 1 1V20c0 .6-.4 1-1 1A17 17 0 0 1 3 4c0-.6.4-1 1-1h3.5c.6 0 1 .4 1 1 0 1.3.2 2.5.6 3.6.1.3 0 .7-.2 1z"/></svg>
        0431 286 517
      </li>
      <li>
        <svg viewBox="0 0 24 24"><path d="M2 5h20v14H2z M2 5l10 8 10-8" /><path d="M2 6.5l10 7.8 10-7.8V5H2z" fill="#1a2029"/></svg>
        rowan@tbk-plumbing.com.au
      </li>
      <li>
        <svg viewBox="0 0 24 24"><path d="M12 2a10 10 0 1 0 0 20 10 10 0 0 0 0-20zm6.9 6h-3a15.6 15.6 0 0 0-1.3-3.9A8 8 0 0 1 18.9 8zM12 4c.8 1.2 1.5 2.5 1.9 4h-3.8c.4-1.5 1.1-2.8 1.9-4zM4.3 14a8 8 0 0 1 0-4h3.4a16 16 0 0 0 0 4zm.8 2h3a15.6 15.6 0 0 0 1.3 3.9A8 8 0 0 1 5.1 16zm3-8h-3a8 8 0 0 1 4.3-3.9C8.8 5.3 8.4 6.6 8.1 8zM12 20c-.8-1.2-1.5-2.5-1.9-4h3.8c-.4 1.5-1.1 2.8-1.9 4zm2.3-6H9.7a14.7 14.7 0 0 1 0-4h4.6a14.7 14.7 0 0 1 0 4zm.3 5.9c.6-1.2 1-2.5 1.3-3.9h3a8 8 0 0 1-4.3 3.9zm1.7-5.9a16 16 0 0 0 0-4h3.4a8 8 0 0 1 0 4z"/></svg>
        www.tbk-plumbing.com.au
      </li>
    </ul>
    <p class="contact-abn"><strong>ABN</strong> - 73 215 904 386</p>
  </div>
</section>

</body>
</html>
```